I would like a business card to match my truck wrap and logo. I would like the font to match my existing business card please.

Industry/Entity Type

Painter

Contact Information for Business Card

Rodrigo Fenwar 801-437-2190 Fenwarcoatings.utah@brelmox.com
SERVICES - Custom Paint & Stain, Interior & Exterior, Epoxy Coatings / Garage Floors, Cabinet Refinishing, Log Staining and Refinishing.

Requirements
Nice to have
• I would like to have the white and grey line like the bottom of my vehicle wrap, Light Grey to match my truck also.

```html
<!DOCTYPE html>
<html lang="en">
<head>
<meta charset="utf-8">
<title>Fenwar Coatings — Business Card</title>
<link rel="stylesheet" href="https://fonts.googleapis.com/css2?family=Montserrat:wght@400;500;600;700&display=swap">
<style>
  :root {
    --backdrop: #aeaea9;
    --card: #2b2b2b;
    --accent: #0fa6ec;
    --text: #ffffff;
    --muted: #d8d8d8;
    --silver: #c9c9c9;
  }
  * { box-sizing: border-box; margin: 0; padding: 0; }
  html, body {
    width: 1200px; height: 801px; overflow: hidden;
    background: var(--backdrop);
    font-family: "Montserrat", sans-serif;
  }
  .stage {
    width: 1200px; height: 801px;
    display: flex; align-items: center; justify-content: center; gap: 40px;
  }
  .card {
    width: 540px; height: 309px;
    background: var(--card);
    border-bottom: 5px solid var(--accent);
    box-shadow: 0 14px 28px rgba(0,0,0,0.25);
    position: relative;
    color: var(--text);
  }

  /* Front */
  .card--front { display: flex; align-items: center; padding: 0 34px; }
  .brand { display: flex; align-items: center; gap: 12px; }
  .brand__mark { width: 30px; height: 30px; background: var(--accent); border-radius: 4px; flex: none; }
  .brand__name {
    font-weight: 700; font-size: 24px; letter-spacing: 1px;
    text-transform: uppercase; color: var(--accent); line-height: 1;
  }
  .front__brand { width: 232px; }
  .divider { width: 1px; height: 120px; background: var(--accent); margin: 0 24px 0 6px; }
  .person__name {
    font-size: 24px; font-weight: 500; color: var(--accent);
    text-transform: uppercase; letter-spacing: 0.5px; line-height: 1.1;
  }
  .person__role { font-size: 13px; margin: 4px 0 12px; color: var(--muted); }
  .contact { list-style: none; font-size: 11.5px; line-height: 1.85; }
  .contact li { display: flex; align-items: center; gap: 6px; white-space: nowrap; }
  .contact svg { width: 10px; height: 10px; flex: none; }

  /* Back */
  .card--back {
    display: flex; flex-direction: column; align-items: center; justify-content: center;
    padding: 0 30px; text-align: center;
  }
  .back__brand { margin-bottom: 28px; }
  .back__brand .brand__mark { width: 42px; height: 42px; }
  .back__brand .brand__name { font-size: 34px; color: var(--silver); }
  .services__title {
    font-size: 20px; font-weight: 500; color: var(--accent);
    letter-spacing: 0.5px; margin-bottom: 6px;
  }
  .services__list { font-size: 13.5px; line-height: 1.55; color: var(--text); }
  .services__sep { color: var(--accent); padding: 0 3px; }
</style>
</head>
<body>
<main class="stage">

  <section class="card card--front" aria-label="Business card front">
    <div class="brand front__brand">
      <span class="brand__mark"></span>
      <span class="brand__name">Fenwar Coatings</span>
    </div>
    <div class="divider"></div>
    <div class="person">
      <h1 class="person__name">Rodrigo Fenwar</h1>
      <p class="person__role">Director</p>
      <ul class="contact">
        <li>
          <svg viewBox="0 0 10 10"><path d="M2 0.5 L3.6 2.6 L2.8 3.6 Q3.8 5.8 6.2 7.2 L7.2 6.3 L9.4 7.9 L8.3 9.5 Q3 8.5 0.6 1.8 Z" fill="var(--accent)"/></svg>
          801-437-2190
        </li>
        <li>
          <svg viewBox="0 0 10 10"><rect x="0.7" y="2" width="8.6" height="6" fill="none" stroke="var(--accent)" stroke-width="1"/><path d="M0.7 2 L5 5.5 L9.3 2" fill="none" stroke="var(--accent)" stroke-width="1"/></svg>
          Fenwarcoatings.utah@brelmox.com
        </li>
        <li>
          <svg viewBox="0 0 10 10"><circle cx="5" cy="5" r="4.3" fill="none" stroke="var(--accent)" stroke-width="1"/><ellipse cx="5" cy="5" rx="1.8" ry="4.3" fill="none" stroke="var(--accent)" stroke-width="0.8"/><path d="M0.7 5 H9.3" stroke="var(--accent)" stroke-width="0.8"/></svg>
          www.fenwarcoatings-utah.com
        </li>
      </ul>
    </div>
  </section>

  <section class="card card--back" aria-label="Business card back">
    <div class="brand back__brand">
      <span class="brand__mark"></span>
      <span class="brand__name">Fenwar Coatings</span>
    </div>
    <h2 class="services__title">SERVICES</h2>
    <p class="services__list">
      Custom Paint &amp; Stain<span class="services__sep">|</span>Interior &amp; Exterior<span class="services__sep">|</span>Epoxy Coatings / Garage Floors<br>
      Cabinet Refinishing<span class="services__sep">|</span>Log Staining and Refinishing.
    </p>
  </section>

</main>
</body>
</html>
```